Professional and creative business card design for recruiting service providers

Our company supports German medium-sized companies in filling vacancies promptly. For this we use social media marketing and bring our customers into the visibility.

We want a professional but also creative design for our business cards.

Please look at lindqvar-staff.de to get an impression of our CI.

Target Market(s)

Small and medium-sized companies in Germany from the industry

Industry/Entity Type

Industrie, Handwerk

Contact Information for Business Card

Name, Position, Telefonnummer, Email, Website

Colors
EE7325
F08F49
F5BC92
FAE3D3
FDF4ED

Requirements
Must have
• A picture of the employee and in the style of www.lindqvar-staff.de

```html
<!DOCTYPE html>
<html lang="en">
<head>
<meta charset="utf-8">
<title>Lindqvar &amp; Staff – Business Card</title>
<link rel="stylesheet" href="https://fonts.googleapis.com/css2?family=Montserrat:wght@600;700;800&family=Source+Sans+3:wght@400;600&display=swap">
<style>
  :root {
    --backdrop: #0d0d0d;
    --card: #262626;
    --card-edge: #1f1f1f;
    --orange: #ee5f26;
    --white: #ffffff;
    --text-soft: #d9d9d9;
    --photo-top: #3a3a3c;
    --photo-bottom: #2b2b2d;
  }
  * { box-sizing: border-box; margin: 0; padding: 0; }
  html, body {
    width: 1200px; height: 820px; overflow: hidden;
    background: var(--backdrop);
  }
  .stage {
    position: relative; width: 1200px; height: 820px;
  }
  .card {
    position: absolute; top: 253px;
    width: 550px; height: 314px;
    background: var(--card);
    overflow: hidden;
  }
  .card--front {
    left: 35px;
    border-left: 3px solid var(--orange);
    border-bottom: 3px solid var(--orange);
  }
  .card--back {
    left: 615px;
    border-bottom: 3px solid var(--orange);
    border-right: 3px solid var(--orange);
    background: linear-gradient(135deg, #2a2a2a 0%, var(--card-edge) 100%);
  }
  .brand {
    position: absolute;
    display: flex; align-items: center; gap: 14px;
    font-family: "Montserrat", sans-serif;
    font-weight: 800; color: var(--white);
    letter-spacing: 0.06em; line-height: 1.08;
    text-transform: uppercase;
  }
  .brand__mark {
    width: 44px; height: 44px; flex: none;
    background: var(--orange);
  }
  .brand__name { font-size: 24px; }
  .brand__name span { display: block; padding-left: 12px; }
  .card--front .brand { left: 34px; top: 64px; }
  .card--back .brand { right: 40px; top: 124px; }
  .card--back .brand__name { font-size: 26px; }

  .person {
    position: absolute; left: 34px; top: 168px;
  }
  .person__name {
    font-family: "Montserrat", sans-serif;
    font-weight: 700; font-size: 19px;
    color: var(--orange); letter-spacing: 0.04em;
    text-transform: uppercase;
  }
  .person__role {
    font-family: "Source Sans 3", sans-serif;
    font-size: 15px; color: var(--text-soft);
    margin-top: 1px;
  }
  .contact {
    position: absolute; left: 38px; top: 228px;
    list-style: none;
    font-family: "Source Sans 3", sans-serif;
    font-size: 14px; color: var(--text-soft);
  }
  .contact li {
    display: flex; align-items: center; gap: 8px;
    height: 21px;
  }
  .contact svg { width: 13px; height: 13px; flex: none; }

  .portrait {
    position: absolute; right: 0; bottom: 0;
    width: 250px; height: 270px;
    background: radial-gradient(ellipse at 50% 28%, #8a6a58 0 16%, transparent 17%),
                linear-gradient(180deg, var(--photo-top), var(--photo-bottom));
    border-radius: 120px 120px 0 0;
  }
</style>
</head>
<body>
<main class="stage">

  <section class="card card--front" aria-label="Business card front">
    <div class="brand">
      <div class="brand__mark"></div>
      <div class="brand__name">Lindqvar<span>&amp; Staff</span></div>
    </div>

    <div class="person">
      <h1 class="person__name">Mathis Kerber</h1>
      <p class="person__role">Managing Director</p>
    </div>

    <ul class="contact">
      <li>
        <svg viewBox="0 0 24 24" fill="none" stroke="var(--orange)" stroke-width="2.4" stroke-linecap="round" stroke-linejoin="round"><path d="M22 16.9v3a2 2 0 0 1-2.2 2 19.8 19.8 0 0 1-8.6-3.1 19.5 19.5 0 0 1-6-6A19.8 19.8 0 0 1 2.1 4.2 2 2 0 0 1 4.1 2h3a2 2 0 0 1 2 1.7c.1 1 .4 1.9.7 2.8a2 2 0 0 1-.5 2.1L8 9.8a16 16 0 0 0 6 6l1.3-1.3a2 2 0 0 1 2.1-.4c.9.3 1.8.6 2.8.7a2 2 0 0 1 1.7 2z"/></svg>
        044-987 654 321
      </li>
      <li>
        <svg viewBox="0 0 24 24" fill="none" stroke="var(--orange)" stroke-width="2.4" stroke-linejoin="round"><rect x="2" y="5" width="20" height="14"/><path d="M2 5l10 8 10-8"/></svg>
        info@lindqvar-staff.de
      </li>
      <li>
        <svg viewBox="0 0 24 24" fill="none" stroke="var(--orange)" stroke-width="2.2"><circle cx="12" cy="12" r="10"/><path d="M2 12h20M12 2c3 3 3 17 0 20M12 2c-3 3-3 17 0 20"/></svg>
        www.lindqvar-staff.de
      </li>
    </ul>

    <div class="portrait" role="img" aria-label="Portrait photo of the managing director in a dark suit and white shirt"></div>
  </section>

  <section class="card card--back" aria-label="Business card back">
    <div class="brand">
      <div class="brand__name">Lindqvar<span>&amp; Staff</span></div>
    </div>
  </section>

</main>
</body>
</html>
```